Fabric Store Business card

Need a business card portraying store logo and up and coming business of quilt fabrics, apparel fabrics, notions and buttons. Our business name is Gilded Thimble and Beyond. Am attaching logo. The design should communicate a growing business and warm atmosphere. Would like address and store hours and contact info displayed on card. Mon - Fri 9:30 to 5:00, Saturday 9:30 to 1:00. Address 784 W Orchard Ave, Newton, KS 67230 email: gildedthimblebeyond@mailvexa.com. Phone and fax 316-527-3486. After hours contact # 620-431-9052 Also like vintage sewing machines and dress forms if it works to incorporate fine, if not thats ok too.
Store

```html
<!DOCTYPE html>
<html lang="en">
<head>
<meta charset="utf-8">
<title>Gilded Thimble and Beyond – Business Card</title>
<link href="https://fonts.googleapis.com/css2?family=Rajdhani:wght@500;600&display=swap" rel="stylesheet">
<style>
  :root {
    --backdrop: #d9dadc;
    --card: #ffffff;
    --card-shade: #f1f1f2;
    --crimson: #a4282e;
    --ink: #3d3d3f;
    --ink-soft: #5c5c60;
  }
  * { box-sizing: border-box; margin: 0; padding: 0; }
  html, body { width: 1052px; height: 1200px; overflow: hidden; }
  body {
    background: var(--backdrop);
    font-family: "Rajdhani", sans-serif;
    position: relative;
  }
  .card {
    position: absolute;
    left: 76px;
    width: 900px;
    height: 514px;
    background: linear-gradient(160deg, var(--card) 55%, var(--card-shade));
    box-shadow: 0 6px 18px rgba(0,0,0,0.12);
    overflow: hidden;
  }
  .card--front { top: 60px; }
  .card--back { top: 626px; }

  .brand {
    position: absolute;
    display: flex;
    align-items: center;
    gap: 18px;
  }
  .brand__dot {
    border-radius: 50%;
    background: var(--crimson);
    flex: none;
  }
  .brand__name {
    color: var(--crimson);
    font-weight: 600;
    line-height: 1;
    white-space: nowrap;
  }
  .card--front .brand { left: 50%; top: 50%; transform: translate(-50%, -50%); }
  .card--front .brand__dot { width: 78px; height: 78px; }
  .card--front .brand__name { font-size: 50px; }

  .card--back .brand { left: 460px; top: 180px; gap: 14px; }
  .card--back .brand__dot { width: 56px; height: 56px; }
  .card--back .brand__name { font-size: 30px; }

  .person { position: absolute; left: 62px; top: 100px; }
  .person__name {
    color: var(--crimson);
    font-size: 40px;
    font-weight: 600;
    letter-spacing: 1px;
    line-height: 1;
  }
  .person__title {
    color: var(--ink);
    font-size: 24px;
    font-weight: 600;
    letter-spacing: 2px;
    margin-top: 6px;
  }
  .rule {
    position: absolute;
    left: 0; top: 190px;
    width: 420px; height: 2px;
    background: var(--crimson);
  }

  .contact-band { position: absolute; left: 0; top: 260px; }
  .contact-list {
    position: absolute;
    left: 150px; top: 260px;
    list-style: none;
    color: var(--ink-soft);
    font-size: 19px;
    font-weight: 500;
    line-height: 1.2;
  }
  .contact-list li { display: flex; align-items: center; height: 34px; white-space: nowrap; }
  .contact-list .phone { height: 36px; }
  .contact-list .address { height: 56px; }
  .contact-list .hours { height: 40px; }
</style>
</head>
<body>

  <section class="card card--front" aria-label="Card front">
    <div class="brand">
      <span class="brand__dot"></span>
      <span class="brand__name">Gilded Thimble and Beyond</span>
    </div>
  </section>

  <section class="card card--back" aria-label="Card back">
    <div class="person">
      <p class="person__name">MARA ELLISON</p>
      <p class="person__title">GENERAL MANAGER</p>
    </div>
    <div class="rule"></div>

    <div class="brand">
      <span class="brand__dot"></span>
      <span class="brand__name">Gilded Thimble and Beyond</span>
    </div>

    <svg class="contact-band" width="140" height="254" viewBox="0 0 140 254" aria-hidden="true">
      <path fill="var(--crimson)" d="M0 0 H110 V12 L122 18 L110 24 V47 L122 53 L110 59 V81 L122 87 L110 93 V126 L122 132 L110 138 V174 L122 180 L110 186 V254 H0 Z"/>
      <path fill="#fff" transform="translate(0,-6)" d="M50 12 c2-2 4-2 5 0 l3 4 c1 2 0 3-1 4 l-1 1 c1 3 3 5 6 6 l1-1 c1-1 2-2 4-1 l4 3 c2 1 2 3 0 5 l-2 2 c-5 3-20-9-20-20 z"/>
      <rect x="48" y="45" width="24" height="16" fill="#fff"/>
      <path d="M48 45 L60 55 L72 45" fill="none" stroke="var(--crimson)" stroke-width="2"/>
      <g fill="none" stroke="#fff" stroke-width="2">
        <circle cx="60" cy="87" r="11"/>
        <ellipse cx="60" cy="87" rx="5" ry="11"/>
        <line x1="49" y1="87" x2="71" y2="87"/>
      </g>
      <path fill="#fff" d="M60 120 c-6 0-10 4-10 10 c0 7 10 16 10 16 s10-9 10-16 c0-6-4-10-10-10 z"/>
      <circle cx="60" cy="130" r="3.5" fill="var(--crimson)"/>
      <g fill="none" stroke="#fff" stroke-width="2">
        <circle cx="60" cy="180" r="10"/>
        <path d="M60 174 V180 L65 183"/>
      </g>
    </svg>

    <ul class="contact-list">
      <li class="phone">316-527-3486 · After hours 620-431-9052</li>
      <li>gildedthimblebeyond@mailvexa.com</li>
      <li>www.gildedthimble.shop</li>
      <li class="address">784 W Orchard Ave,<br>Newton, KS 67230</li>
      <li class="hours">Mon–Fri 9:30–5:00 · Sat 9:30–1:00</li>
    </ul>
  </section>

</body>
</html>
```